Stationery Design Project for Marketing Consultancy

I have started a new consultancy business and require the following elements to be designed using existing logo:
• Business card
• Letterhead
• Envelope (DL, C4, C5)
• Microsoft word template for report writing
• A4 Presentation Folder
• Powerpoint template
COPY FOR FRONT AND BACK OF BUSINESS CARD
logo
'Measurable Marketing. Epic Results' slogan (but no need to use existing lockup with logo)
name, B Bus. Mktg, Grad Dip Digital Mktg, CPM (post nominal abbreviations in smaller font)
mobile: 04XX-XXX-XXX (I will give details to the winner to add)
website: www.tolvarin.com.au
email: info@tolvarin.com.au
COPY FOR LETTERHEAD
Logo
Company Name
Please, submit your designs that include business card, letterhead and envelope. Once selected the winner will be asked to complete the project by creating the rest of the artwork.
FINAL FILES
Print ready files to be supplied as well as Indesign files so that minor amends can be made if necessary in future.
• Layered vectors in EPS & PDF
• Screen quality JPEG & PNGs
ABOUT THE BUSINESS: TOLVARIN
I work with clients to understand their business challenges, developing and executing measurable marketing strategies tied to key business metrics. Services include:
Services include:
• Business planning and business development
• Marketing and brand strategy
• Insight-driven integrated campaigns
• Loyalty programs and retention marketing
• Marketing automation
• Direct marketing (traditional and digital)
• Content strategy and development
Hi everyone,
Target Market(s)
Corporate decision makers (heads of marketing, general managers etc) and small to medium sized business owners. Predominately male aged 35+
Industry/Entity Type
Marketing
Requirements
Must have
- BRAND PERSONALITY
The successful design will communicate brand personality. I am a professional, results-driven entrepreneur, but want to show off my creative flair.
MEMORABILITY
Looking for a unique and eye-catching design. Am considering special printing effects (die cuts, letterpress, interactive elements, embossing, foiling etc) or a striking minimalist approach.
Nice to have
- I have a mission that could be incorporated on reverse if room -
Turning insights into actions & passion into profit.
Should not have
- Use of pink or green.

```html
<!DOCTYPE html>
<html lang="en">
<head>
<meta charset="utf-8">
<title>Tolvarin – Business Card</title>
<link href="https://fonts.googleapis.com/css2?family=Open+Sans:wght@600;700&family=Questrial&display=swap" rel="stylesheet">
<style>
  :root {
    --backdrop: #464646;
    --card-black: #0b0b0b;
    --card-edge: #151515;
    --silver: #e9e9e9;
    --text-soft: #d6d6d6;
    --text-muted: #bdbdbd;
  }
  * { margin: 0; padding: 0; box-sizing: border-box; }
  html, body {
    width: 1200px;
    height: 1000px;
    overflow: hidden;
    background: var(--backdrop);
  }
  .canvas {
    position: relative;
    width: 1200px;
    height: 1000px;
  }
  .business-card {
    position: absolute;
    left: 100px;
    top: 214px;
    width: 1000px;
    height: 571px;
    border-radius: 22px;
    background: linear-gradient(160deg, var(--card-edge) 0%, var(--card-black) 55%, #070707 100%);
    box-shadow: 0 10px 30px rgba(0,0,0,0.35);
  }
  .brand-block {
    position: absolute;
    left: 91px;
    top: 340px;
    width: 340px;
  }
  .brand-name {
    font-family: "Open Sans", sans-serif;
    font-weight: 700;
    font-size: 60px;
    line-height: 1;
    letter-spacing: 1px;
    color: var(--silver);
  }
  .brand-slogan {
    margin-top: 10px;
    font-family: "Open Sans", sans-serif;
    font-weight: 600;
    font-size: 14.5px;
    letter-spacing: 1.2px;
    color: var(--silver);
    white-space: nowrap;
  }
  .contact-block {
    position: absolute;
    left: 585px;
    top: 212px;
  }
  .person-name {
    font-family: "Open Sans", sans-serif;
    font-weight: 700;
    font-size: 26px;
    letter-spacing: 1px;
    color: var(--text-soft);
  }
  .person-role {
    font-family: "Questrial", sans-serif;
    font-size: 22px;
    color: var(--text-muted);
    margin-top: 2px;
  }
  .contact-list {
    list-style: none;
    margin-top: 48px;
  }
  .contact-item {
    display: flex;
    align-items: center;
    gap: 18px;
    height: 37px;
    font-family: "Questrial", sans-serif;
    font-size: 22px;
    color: var(--text-soft);
  }
  .contact-icon {
    width: 26px;
    height: 26px;
    flex: none;
  }
</style>
</head>
<body>
<main class="canvas">
  <section class="business-card" aria-label="Business card front">
    <div class="brand-block">
      <div class="brand-name">TOLVARIN</div>
      <div class="brand-slogan">CLEAR STRATEGY. PROVEN GROWTH.</div>
    </div>

    <div class="contact-block">
      <div class="person-name">MARCUS HALE</div>
      <div class="person-role">Managing Director</div>
      <ul class="contact-list">
        <li class="contact-item">
          <svg class="contact-icon" viewBox="0 0 26 26" aria-hidden="true">
            <circle cx="13" cy="13" r="11.5" fill="none" stroke="#cfcfcf" stroke-width="1.6"/>
            <rect x="9" y="6.5" width="8" height="13" rx="1.5" fill="none" stroke="#cfcfcf" stroke-width="1.5"/>
            <line x1="11.5" y1="17" x2="14.5" y2="17" stroke="#cfcfcf" stroke-width="1.3"/>
          </svg>
          <span>+0491-208-617</span>
        </li>
        <li class="contact-item">
          <svg class="contact-icon" viewBox="0 0 26 26" aria-hidden="true">
            <circle cx="13" cy="13" r="11.5" fill="#cfcfcf"/>
            <rect x="7" y="9" width="12" height="8.5" rx="1" fill="#0b0b0b"/>
            <polyline points="7.5,9.5 13,14 18.5,9.5" fill="none" stroke="#cfcfcf" stroke-width="1.2"/>
          </svg>
          <span>info@tolvarin.com.au</span>
        </li>
        <li class="contact-item">
          <svg class="contact-icon" viewBox="0 0 26 26" aria-hidden="true">
            <g fill="none" stroke="#cfcfcf" stroke-width="1.5">
              <circle cx="13" cy="13" r="11"/>
              <ellipse cx="13" cy="13" rx="5" ry="11"/>
              <line x1="2" y1="13" x2="24" y2="13"/>
              <path d="M4 7.5 H22 M4 18.5 H22"/>
            </g>
          </svg>
          <span>www.tolvarin.com.au</span>
        </li>
      </ul>
    </div>
  </section>
</main>
</body>
</html>
```